Tiroler party ecommerce site

We have a eCommerce site that needs a redesign. What we need are 3 pages: a frontpage, a product listing page and a product page.

The look has to be:
fun, modern, fresh, bright, professional look but not corporate.

Some content keywords are :
Carnival, oktoberfesten, tirol, dirndl, leder hosen, beer, women with big breast (no porn! just fun)

Some functional hints :

The frontpage needs to give a good impression of all the products on the site.
There should also be some space for campaigns or banners on the frontpage.

The product listing page should have facets (search options) and a search field.

The product page should have a few boxes such as related products, others viewed, comments etc.. (your average product page content)

All pages should show a small cart button or box and off course a kick ass menu!

Some links :

The current site http://www.feestkraamwinkel.nl/

We couldn't find any site to show as inspiration most party sites are very bad!.

```html
<!DOCTYPE html>
<html lang="nl">
<head>
<meta charset="utf-8">
<title>Feestkraamwinkel – Tiroler party shop</title>
<link href="https://fonts.googleapis.com/css2?family=Arvo:wght@400;700&family=Open+Sans:wght@300;400;600;700&display=swap" rel="stylesheet">
<style>
:root{
  --page:#efe9d9;
  --topbar:#4a2615;
  --accent:#ef5a24;
  --accent-dark:#d9461a;
  --sky:#54bde3;
  --btn-blue:#5ac3e6;
  --brown:#c48d4c;
  --brown-dark:#a86f35;
  --red:#e94b2b;
  --yellow:#f3b725;
  --ink:#3b2a1f;
  --text:#5d5148;
  --muted:#9a8f86;
  --white:#ffffff;
  --line:#d8cfbd;
}
*{box-sizing:border-box;margin:0;padding:0}
html,body{width:1200px;height:2654px;overflow:hidden}
body{background:var(--page);font-family:"Open Sans",Arial,sans-serif;color:var(--text);position:relative}
a{color:inherit;text-decoration:none}
.abs{position:absolute}

/* top bar */
.topbar{left:0;top:0;width:1200px;height:30px;background:var(--topbar);color:#e8d9c8;font-size:13px}
.topbar .links{position:absolute;left:105px;top:0;display:flex;height:30px}
.topbar .links a{padding:0 12px;line-height:30px}
.topbar .links a.active{background:var(--accent);color:#fff;font-weight:600}
.topbar .right{position:absolute;right:118px;top:0;display:flex;gap:34px;line-height:30px}
.topbar .right span{display:flex;align-items:center;gap:7px}

/* header */
.header{left:0;top:30px;width:1200px;height:103px;background:var(--page)}
.logo{position:absolute;left:103px;top:36px;font-family:"Arvo",serif;font-weight:700;font-size:30px;color:var(--topbar);letter-spacing:1px}
.search{position:absolute;left:516px;top:35px;width:309px;height:40px;background:#fff;border:1px solid #ddd;display:flex}
.search input{flex:1;border:0;padding:0 12px;font-family:inherit;font-size:13px;color:#777;background:transparent}
.search button{width:40px;border:0;background:var(--accent);display:flex;align-items:center;justify-content:center}
.cart{position:absolute;left:952px;top:35px;width:133px;height:40px;background:var(--topbar);color:#fff;display:flex;align-items:center;gap:9px;padding-left:14px;font-size:14px;font-weight:600}
.cart .count{margin-left:auto;margin-right:8px;width:24px;height:24px;background:var(--accent);border-radius:3px;text-align:center;line-height:24px;font-size:13px}

/* nav */
.nav{left:0;top:133px;width:1200px;height:59px;background:#fff;border-bottom:1px solid #e5dfd2}
.nav ul{list-style:none;display:flex;justify-content:space-between;padding:0 86px;height:59px;align-items:center}
.nav li{font-size:15px;font-weight:600;color:var(--ink)}
.nav li .caret{font-size:10px;margin-left:5px}

/* hero */
.hero{left:0;top:192px;width:1200px;height:474px;background:var(--sky);overflow:hidden}
.hero-photo{position:absolute;left:0;top:0;width:650px;height:474px;background:linear-gradient(110deg,#e6d7b8 0%,#d8b98a 40%,#8fc6d8 85%,var(--sky) 100%)}
.badge-new{position:absolute;left:693px;top:73px;width:70px;height:70px;background:var(--yellow);color:#fff;font-weight:700;font-size:15px;display:flex;align-items:center;justify-content:center}
.hero h1{position:absolute;left:693px;top:140px;font-weight:300;color:#fff;font-size:46px;line-height:52px}
.hero p{position:absolute;left:693px;top:255px;width:330px;color:#fff;font-size:18px;line-height:26px}
.hero .cta{position:absolute;left:693px;top:339px;width:206px;height:40px;background:var(--accent);color:#fff;font-weight:600;font-size:15px;text-align:center;line-height:40px}
.hero .arrow{position:absolute;top:220px;width:52px;height:52px;border:2px solid #fff;border-radius:50%;display:flex;align-items:center;justify-content:center}
.hero .dots{position:absolute;left:700px;top:410px;display:flex;gap:12px}
.hero .dots i{width:10px;height:10px;border-radius:50%;background:#b5e3f2}
.hero .dots i.on{background:var(--yellow)}

/* welcome */
.welcome{left:0;top:694px;width:1200px;text-align:center}
.welcome h2{font-family:"Arvo",serif;font-weight:700;font-size:34px;color:var(--ink);letter-spacing:.5px}
.welcome p{width:960px;margin:30px auto 0;font-size:16px;line-height:24px;color:var(--text)}

/* promos */
.promo{top:876px;width:309px;height:174px;color:#fff;overflow:hidden}
.promo .art{position:absolute;right:0;top:0;width:130px;height:174px}
.promo h3{position:absolute;left:18px;top:14px;font-family:"Arvo",serif;font-weight:700;font-size:48px;letter-spacing:.5px}
.promo p{position:absolute;left:18px;top:82px;width:160px;font-size:12px;line-height:16px;font-weight:600}
.promo .btn{position:absolute;left:18px;top:130px;width:96px;height:26px;background:var(--btn-blue);font-size:10px;font-weight:700;text-align:center;line-height:26px}
.promo.new{left:118px;background:var(--brown)}
.promo.hot{left:451px;background:var(--red)}
.promo.sale{left:781px;background:var(--yellow)}

/* section headings */
.section-title{left:109px;width:970px;display:flex;align-items:center;gap:30px}
.section-title::before,.section-title::after{content:"";flex:1;height:1px;background:var(--line)}
.section-title h2{font-family:"Arvo",serif;font-weight:700;font-size:28px;color:var(--ink)}

/* product cards */
.grid{left:109px;width:970px;display:flex;justify-content:space-between}
.card{width:226px;height:322px;background:#fff;border:1px solid #e3ddd0;padding:0 0 0 0;position:relative}
.card .img{width:224px;height:225px}
.card .name{position:absolute;left:14px;top:244px;font-size:14px;color:var(--ink)}
.card .price{position:absolute;left:14px;top:280px;font-size:17px;color:var(--ink)}
.card .shop{position:absolute;right:14px;top:280px;width:86px;height:24px;background:var(--btn-blue);color:#fff;font-size:10px;font-weight:700;text-align:center;line-height:24px}

/* newsletter */
.signup{left:109px;top:1996px;width:970px;height:250px;background:#fff;border:1px solid #e3ddd0;text-align:center}
.signup h2{margin-top:22px;font-family:"Arvo",serif;font-weight:700;font-size:28px;color:var(--ink)}
.signup p{margin:14px auto 0;width:480px;font-size:15px;line-height:24px;color:var(--ink)}
.signup .field{position:absolute;left:348px;top:122px;width:274px;height:40px;border:1px solid #ddd;font-size:14px;color:#aaa;line-height:38px}
.signup .go{position:absolute;left:348px;top:176px;width:274px;height:46px;background:var(--accent);color:#fff;font-size:14px;font-weight:700;line-height:46px}

/* footer */
.footer{left:0;top:2308px;width:1200px;height:257px;background:var(--brown);color:#fff}
.footer h4{position:absolute;top:38px;font-size:17px;font-weight:700}
.footer ul{position:absolute;top:82px;list-style:none;font-size:15px;line-height:23px;color:#fbeede}
.social{position:absolute;left:808px;top:100px;display:flex;gap:12px}
.social i{width:36px;height:36px;background:#d9aa74;display:block}
.legal{left:0;top:2565px;width:1200px;height:89px;background:var(--brown-dark);color:#fff;text-align:center}
.legal p{padding-top:16px;font-size:15px}
.pay{display:flex;justify-content:center;gap:8px;margin-top:12px;align-items:center}
.pay i{display:block;width:46px;height:28px;border-radius:3px;background:#f1e3d0}
.pay i.wide{width:90px;background:#e7d2b7}
</style>
</head>
<body>

<div class="abs topbar">
  <div class="links"><a class="active">About</a><a>Information ▾</a><a>Contact</a></div>
  <div class="right">
    <span><svg width="12" height="12" viewBox="0 0 24 24"><path fill="#e8d9c8" d="M6.6 10.8c1.4 2.8 3.8 5.1 6.6 6.6l2.2-2.2c.3-.3.7-.4 1-.2 1.1.4 2.3.6 3.6.6.6 0 1 .4 1 1V20c0 .6-.4 1-1 1C10.6 21 3 13.4 3 4c0-.6.4-1 1-1h3.5c.6 0 1 .4 1 1 0 1.3.2 2.5.6 3.6.1.3 0 .7-.2 1l-2.3 2.2z"/></svg>010 555 48 20</span>
    <span><svg width="12" height="12" viewBox="0 0 24 24"><circle cx="12" cy="8" r="5" fill="#e8d9c8"/><path fill="#e8d9c8" d="M2 22c0-5 4.5-8 10-8s10 3 10 8z"/></svg>Login / Register</span>
  </div>
</div>

<header class="abs header">
  <div class="logo">FEESTKRAAMWINKEL</div>
  <div class="search"><input value="What are you looking for ?"><button><svg width="16" height="16" viewBox="0 0 24 24"><circle cx="10" cy="10" r="7" fill="none" stroke="#fff" stroke-width="3"/><path d="M15 15l6 6" stroke="#fff" stroke-width="3"/></svg></button></div>
  <a class="cart"><svg width="16" height="15" viewBox="0 0 24 22"><path fill="#fff" d="M0 1h4l3 12h13l3-9H7" /><circle cx="9" cy="18" r="2" fill="#fff"/><circle cx="18" cy="18" r="2" fill="#fff"/></svg>Cart ▾<span class="count">0</span></a>
</header>

<nav class="abs nav">
  <ul>
    <li>Tiroler Kleding<span class="caret">▼</span></li>
    <li>Kleding Accessories<span class="caret">▼</span></li>
    <li>Tiroler Schorten</li>
    <li>Tiroler Hoeden<span class="caret">▼</span></li>
    <li>Decoraties<span class="caret">▼</span></li>
    <li>Cadeau artikelen<span class="caret">▼</span></li>
  </ul>
</nav>

<section class="abs hero">
  <div class="hero-photo" role="img" aria-label="Woman in a dirndl holding beer mugs"></div>
  <a class="arrow" style="left:16px"><svg width="16" height="16" viewBox="0 0 16 16"><path d="M11 2L5 8l6 6" fill="none" stroke="#fff" stroke-width="2.5"/></svg></a>
  <a class="arrow" style="left:1110px"><svg width="16" height="16" viewBox="0 0 16 16"><path d="M5 2l6 6-6 6" fill="none" stroke="#fff" stroke-width="2.5"/></svg></a>
  <div class="badge-new">NEW</div>
  <h1>Octoberfest<br>2014 Collection</h1>
  <p>Nunc non fermentum nunc. Sed ut ante eget leo tempor consequat sit amet eu orci. Donec dignissim dolor eget.</p>
  <a class="cta">VIEW COLLECTION</a>
  <div class="dots"><i class="on"></i><i></i><i></i></div>
</section>

<section class="abs welcome">
  <h2>Willkommen in Tirol, Tyrol and welcome to our shop!</h2>
  <p>Feestkraamwinkel.nl is the first shop specializing in Tyrolean articles. So if you have a Tyrolean party, or just looking for Tyrolean carnival clothes , you are guaranteed to come to the right place. Of course we also have everything for a great apres ski party in our range.</p>
</section>

<a class="abs promo new"><h3>New!</h3><p>You would have to be half mad to dream me up.</p><span class="btn">VIEW NOW</span><div class="art" role="img" aria-label="Baby in Tyrolean outfit" style="background:linear-gradient(180deg,#d7a46a,#b47a3e)"></div></a>
<a class="abs promo hot"><h3>Hot!</h3><p>You would have to be half mad to dream me up.</p><span class="btn">VIEW NOW</span><div class="art" role="img" aria-label="Crossed wooden axes" style="background:linear-gradient(180deg,#ee6a4a,#d83f22)"></div></a>
<a class="abs promo sale"><h3>Sale!</h3><p>You would have to be half mad to dream me up.</p><span class="btn">VIEW NOW</span><div class="art" role="img" aria-label="Legs in white knee socks and dirndl" style="background:linear-gradient(180deg,#f6c84c,#e9a71a)"></div></a>

<div class="abs section-title" style="top:1108px"><h2>New Stock</h2></div>
<div class="abs grid" style="top:1180px">
  <div class="card"><div class="img" role="img" aria-label="Woman in blue and yellow beer girl costume" style="background:linear-gradient(180deg,#f5f2ea,#e9e2d2)"></div><div class="name">Biermeisje</div><div class="price">€ 23.90</div><a class="shop">SHOP NOW</a></div>
  <div class="card"><div class="img" role="img" aria-label="Man wearing green felt Tyrolean hat" style="background:linear-gradient(180deg,#f5f2ea,#e9e2d2)"></div><div class="name">Hoed tiroler groen vilt</div><div class="price">€15,80</div><a class="shop">SHOP NOW</a></div>
  <div class="card"><div class="img" role="img" aria-label="Man in beige lederhosen and checked shirt" style="background:linear-gradient(180deg,#f5f2ea,#e9e2d2)"></div><div class="name">Bayernhose beige</div><div class="price">€ 13.50</div><a class="shop">SHOP NOW</a></div>
  <div class="card"><div class="img" role="img" aria-label="Woman wearing red braided wig" style="background:linear-gradient(180deg,#f5f2ea,#e9e2d2)"></div><div class="name">Gretchen Wig smooth</div><div class="price">€ 23.10</div><a class="shop">SHOP NOW</a></div>
</div>

<div class="abs section-title" style="top:1539px"><h2>Best Sellers</h2></div>
<div class="abs grid" style="top:1610px">
  <div class="card"><div class="img" role="img" aria-label="Man wearing green felt Tyrolean hat" style="background:linear-gradient(180deg,#f5f2ea,#e9e2d2)"></div><div class="name">Hoed tiroler groen vilt</div><div class="price">€4,90</div><a class="shop">SHOP NOW</a></div>
  <div class="card"><div class="img" role="img" aria-label="Woman in blue and yellow beer girl costume" style="background:linear-gradient(180deg,#f5f2ea,#e9e2d2)"></div><div class="name">Biermeisje</div><div class="price">€ 11.90</div><a class="shop">SHOP NOW</a></div>
  <div class="card"><div class="img" role="img" aria-label="Woman wearing red braided wig" style="background:linear-gradient(180deg,#f5f2ea,#e9e2d2)"></div><div class="name">Gretchen Wig smooth</div><div class="price">€ 12.40</div><a class="shop">SHOP NOW</a></div>
  <div class="card"><div class="img" role="img" aria-label="Man in beige lederhosen and checked shirt" style="background:linear-gradient(180deg,#f5f2ea,#e9e2d2)"></div><div class="name">Bayernhose beige</div><div class="price">€ 23.90</div><a class="shop">SHOP NOW</a></div>
</div>

<section class="abs signup">
  <h2>Sign up &amp; Save</h2>
  <p>Sign up for our newsletter now and be the first to know about sale offers and news exclusive to feestkraamwinkel</p>
  <div class="field">Enter your email address</div>
  <a class="go">SIGN UP</a>
</section>

<footer class="abs footer">
  <h4 style="left:115px">The Company</h4>
  <ul style="left:115px"><li>About Us</li><li>Contact</li><li>How to buy</li><li>FAQ's</li></ul>
  <h4 style="left:442px">Customer Service</h4>
  <ul style="left:442px"><li>Need help? Give us a shout.</li><li>Customer hotline: 0800 555 0192</li><li>Return/refund policy</li></ul>
  <h4 style="left:808px">Connect with us</h4>
  <div class="social"><i></i><i></i><i></i><i></i><i></i></div>
</footer>

<div class="abs legal">
  <p>Feestkraamwinkel.nl | Lindenlaan 14 | 7311 KB APELDOORN | Feestkraamwinkel.nl is onderdeel van Lachbox BV</p>
  <div class="pay"><i></i><i></i><i></i><i></i><i></i><i class="wide"></i></div>
</div>

</body>
</html>
```